Harborview Estates Business Card for Apartment Buildings

Create business cards for resident managers who run apartment buildings. The audience is the public who are searching for apartment rentals, and current residents who live at the apartment building. Key design element will be incorporating the company logo, however, the logo cannot dominate. The building name and manager name are more important than the logo. Current business card design leaves little room for copy, so we may need to reduce the size on the current card to allow for more space for copy.

Target Market(s)

Adults 18-65 years of age, who are looking for an apartment rental, plus current residents who live at our apartment buildings.

Industry/Entity Type

Property Management

Contact Information for Business Card

A major design element will be use of the company logo. Important property and manager contact information must be part of the design. The size of the logo will need to be reduced to make room for building and manager contact copy.

Font styles to use
Sans Serif

Colors
3176b5
000000
959595
ffffff

Requirements
Must have
• 1) Incorporate the company logo.
• 2) Use the company colors (dark blue, black/grey, over white).
• 3) FEATURE THE BUILDING NAME
• 4) FEATURE THE MANAGER NAME
• 5) The company name is less important than BUILDING and MANAGER
• 6) Manager contact information
• **SEE ATTACHED CREATIVE BRIEF**
Nice to have
• 1) Back of card logo watermark
• 2) Ability to write notes on back of carfd
Should not have
• Avoid letting the company logo dominate the card, the building name and manager are more important than the company logo.

```html
<!DOCTYPE html>
<html lang="en">
<head>
<meta charset="utf-8">
<title>Harborview Estates – Resident Manager Business Card</title>
<link rel="stylesheet" href="https://fonts.googleapis.com/css2?family=Roboto:wght@400;500;700&family=Roboto+Condensed:wght@700&display=swap">
<style>
  :root {
    --brand-blue: #3176b5;
    --ink-blue: #1f6aab;
    --text-grey: #4a4a4a;
    --mid-grey: #959595;
    --card-white: #f4f4f4;
    --backdrop: #2b2b2b;
    --watermark: #e3e3e3;
  }
  * { margin: 0; padding: 0; box-sizing: border-box; }
  html, body {
    width: 1200px; height: 960px; overflow: hidden;
    background: var(--backdrop);
    font-family: "Roboto", Arial, sans-serif;
  }
  .card {
    position: absolute;
    width: 600px; height: 343px;
    background: var(--card-white);
    overflow: hidden;
  }
  .card--front { left: 314px; top: 113px; }
  .card--back  { left: 311px; top: 472px; }

  .manager { position: absolute; left: 41px; top: 49px; }
  .manager__name {
    font-family: "Roboto Condensed", "Arial Narrow", sans-serif;
    font-weight: 700; font-size: 24px; color: var(--ink-blue); line-height: 1.1;
  }
  .manager__title { font-size: 15px; font-weight: 400; color: var(--text-grey); margin-top: 2px; }

  .company {
    position: absolute; right: 44px; top: 58px;
    display: flex; align-items: center; gap: 10px;
    white-space: nowrap;
  }
  .company__square { width: 22px; height: 22px; background: var(--brand-blue); flex: none; }
  .company__name {
    font-size: 20px; font-weight: 700; color: var(--brand-blue);
    letter-spacing: 0.5px; text-transform: uppercase;
  }

  .property { position: absolute; left: 36px; top: 212px; }
  .property__name { font-size: 23px; font-weight: 700; color: var(--ink-blue); line-height: 1.1; }
  .property__address { font-size: 14.5px; color: var(--text-grey); margin-top: 3px; }

  .contact { margin-top: 9px; font-size: 14.5px; color: var(--text-grey); white-space: nowrap; }
  .contact__row { display: flex; align-items: center; gap: 4px; line-height: 19px; }
  .contact__item { display: inline-flex; align-items: center; gap: 6px; margin-right: 2px; }
  .contact__icon { width: 14px; height: 14px; fill: var(--ink-blue); flex: none; }

  .watermark {
    position: absolute; inset: 0;
    display: flex; align-items: center; justify-content: center;
    padding: 0 40px;
    text-align: center; white-space: nowrap;
    font-size: 40px; font-weight: 700; color: var(--watermark);
    text-transform: uppercase; letter-spacing: 2px;
  }
</style>
</head>
<body>
  <section class="card card--front">
    <div class="manager">
      <div class="manager__name">Marisol Delgado</div>
      <div class="manager__title">Resident Manager</div>
    </div>

    <div class="company">
      <span class="company__square"></span>
      <span class="company__name">Harborview Estates LLC</span>
    </div>

    <div class="property">
      <div class="property__name">Cedar Grove Apartments</div>
      <div class="property__address">2845 Linden Avenue, Bayside, CA 92110</div>

      <div class="contact">
        <div class="contact__row">
          <span class="contact__item">
            <svg class="contact__icon" viewBox="0 0 16 16"><path d="M3.6 1.2l2.3 2.6-1.3 1.7c.9 2 2.6 3.7 4.6 4.6l1.7-1.3 2.6 2.3-1.2 2.3C7.5 14.2 1.8 8.5 1.4 3z"/></svg>
            555-210-4471
          </span>
          <span class="contact__item">
            <svg class="contact__icon" viewBox="0 0 16 16"><path d="M4.5 0h7a1 1 0 0 1 1 1v14a1 1 0 0 1-1 1h-7a1 1 0 0 1-1-1V1a1 1 0 0 1 1-1zm.6 2v10.5h5.8V2zM8 13.3a.9.9 0 1 0 0 1.8.9.9 0 0 0 0-1.8z"/></svg>
            555-318-6620
          </span>
          <span class="contact__item">
            <svg class="contact__icon" viewBox="0 0 16 16"><path d="M4 1h8v4H4zM1 6h14v7h-3v2H4v-2H1zm4 5v3h6v-3z"/></svg>
            555-402-7350
          </span>
        </div>
        <div class="contact__row">
          <span class="contact__item">
            <svg class="contact__icon" viewBox="0 0 16 16"><path d="M1 3h14v1.2L8 9 1 4.2zm0 2.6l7 4.8 7-4.8V13H1z"/></svg>
            marisol@harborviewest.com
          </span>
          <span class="contact__item">
            <svg class="contact__icon" viewBox="0 0 16 16"><path d="M8 1a7 7 0 1 0 0 14A7 7 0 0 0 8 1zm-1 2.2c-.8 1-1.2 2-1.3 3.3H3.1A5 5 0 0 1 7 3.2zM3.1 9.5h2.6c.1 1.3.5 2.3 1.3 3.3a5 5 0 0 1-3.9-3.3zm4.6 0h.6v3.8c-.3 0-.6-1.6-.6-3.8zm1.3 3.3c.8-1 1.2-2 1.3-3.3h2.6A5 5 0 0 1 9 12.8zm1.3-6.3C10.2 5.2 9.8 4.2 9 3.2a5 5 0 0 1 3.9 3.3z"/></svg>
            harborviewest.com
          </span>
        </div>
      </div>
    </div>
  </section>

  <section class="card card--back">
    <div class="watermark">Harborview Estates</div>
  </section>
</body>
</html>
```